Veterinary Pylon

My veterinary clinic is not clearly visible from the street and I want to place a Pylon next to my driveway. I want a modern, elegant straight Design, the Photo shows the sheduled place. One can see the clinic on our Homepage: www.tailbright-vethaus.at
The last pictures are examples for pylones I like

Target Market(s)

the passing cars often miss my entry...I want to show where to turn left

Colors
3276b5
33a6d7
00a990

Requirements
Must have
• High value, simple elegance, size: 250cm (high) x 100cm (width)
Nice to have
• Our Logo, arrow(?)

A special Text is not necessary but this will be an option:

Biegen sie hier ab und wir biegen es wieder hin!
Should not have
• Too much Color, the colors I have chosen are the possible colors but it‘s not necessary to use them.

```html
<!DOCTYPE html>
<html lang="de">
<head>
<meta charset="utf-8">
<title>Tailbright Vethaus – Pylon</title>
<link rel="stylesheet" href="https://fonts.googleapis.com/css2?family=Archivo+Black&display=swap">
<style>
  :root {
    --navy: #134a93;
    --sky: #2dbadf;
    --sign-blue: #00aad6;
    --wave-mist: #e3f4f9;
    --wave-deep: #1a6aa8;
    --paper: #ffffff;
  }
  html, body {
    margin: 0;
    padding: 0;
    width: 1200px;
    height: 3000px;
    overflow: hidden;
    background: var(--paper);
  }
  .pylon {
    position: relative;
    width: 1200px;
    height: 3000px;
    overflow: hidden;
    background: var(--paper);
  }
  .pylon__waves {
    position: absolute;
    inset: 0;
    width: 1200px;
    height: 3000px;
  }
  .brand {
    position: absolute;
    left: 0;
    right: 0;
    top: 470px;
    display: flex;
    flex-direction: column;
    align-items: center;
  }
  .brand__dot {
    width: 300px;
    height: 300px;
    border-radius: 50%;
    background: var(--sky);
    margin-bottom: 150px;
  }
  .brand__name {
    margin: 0;
    font-family: "Archivo Black", "Arial Black", sans-serif;
    font-weight: 400;
    color: var(--navy);
    text-transform: uppercase;
    text-align: center;
    font-size: 118px;
    line-height: 1.08;
    letter-spacing: 2px;
  }
  .turn-sign {
    position: absolute;
    left: 424px;
    top: 1475px;
    width: 380px;
    height: 380px;
  }
</style>
</head>
<body>
<main class="pylon">
  <svg class="pylon__waves" viewBox="0 0 1030 2576" preserveAspectRatio="none" aria-hidden="true">
    <defs>
      <linearGradient id="lowerStroke" x1="0" y1="0" x2="1" y2="0">
        <stop offset="0" stop-color="#1a5e9e"/>
        <stop offset="1" stop-color="#33a6d7"/>
      </linearGradient>
    </defs>
    <!-- top band -->
    <path fill="var(--wave-mist)" d="M0,0 H1030 V165 C960,90 830,55 710,55 C570,55 460,100 360,148 C250,200 120,195 0,132 Z"/>
    <path fill="none" stroke="var(--sky)" stroke-width="11" stroke-linecap="round"
          d="M10,172 C120,225 250,238 370,188 C500,126 620,98 720,93 C860,86 975,128 1030,182"/>
    <!-- bottom band -->
    <path fill="var(--wave-mist)" d="M0,1830 C120,1762 240,1752 360,1808 C480,1868 600,1900 720,1903 C880,1905 980,1850 1030,1795 V2576 H0 Z"/>
    <path fill="none" stroke="url(#lowerStroke)" stroke-width="12" stroke-linecap="round"
          d="M12,1786 C120,1728 240,1716 360,1772 C480,1832 600,1866 720,1869 C860,1871 968,1830 1030,1777"/>
  </svg>

  <header class="brand">
    <div class="brand__dot"></div>
    <h1 class="brand__name">Tailbright<br>Vethaus</h1>
  </header>

  <svg class="turn-sign" viewBox="0 0 330 330" role="img" aria-label="Hier links abbiegen">
    <circle cx="165" cy="165" r="162" fill="none" stroke="var(--sign-blue)" stroke-width="2"/>
    <circle cx="165" cy="165" r="157" fill="var(--sign-blue)"/>
    <polygon fill="var(--paper)"
             points="28,165 93,100 157,100 115,142 298,142 298,185 115,185 157,229 93,229"/>
  </svg>
</main>
</body>
</html>
```